Meadowlark Scalp Parlour jojoba oil

Hello there!
I am looking to have a label created for a jojoba oil product I am launching. I have attached the logo of my company below. The label should have the following information on it as well:
Ingredients: pure jojoba oil
Size of the bottle: 118ml
And there might be more but I am working on this and will keep you posted.

```html
<!DOCTYPE html>
<html lang="en">
<head>
<meta charset="utf-8">
<title>Meadowlark Scalp Parlour – Jojoba Oil Label</title>
<link rel="stylesheet" href="https://fonts.googleapis.com/css2?family=Montserrat:wght@500&family=Oswald:wght@500;600&family=Roboto:wght@400&family=Roboto+Condensed:wght@400&display=swap">
<style>
  :root {
    --canvas-bg: #efe9df;
    --label-white: #ffffff;
    --rose-dark: #a3463a;
    --rose-mid: #c0685b;
    --rose-light: #dc9d92;
    --ink: #231f20;
    --text-light: #ffffff;
    --fruit-light: #e0704a;
    --fruit-dark: #8c2a1c;
  }
  * { margin: 0; padding: 0; box-sizing: border-box; }
  html, body {
    width: 1200px;
    height: 795px;
    overflow: hidden;
    background: var(--canvas-bg);
  }
  .canvas {
    position: relative;
    width: 1200px;
    height: 795px;
  }
  .label {
    position: absolute;
    left: 208px;
    top: 45px;
    width: 784px;
    height: 705px;
    overflow: hidden;
    background: var(--label-white);
    box-shadow: 0 0 0 1px rgba(0,0,0,0.15);
  }
  .label-shapes {
    position: absolute;
    inset: 0;
  }
  .brand-name {
    position: absolute;
    left: 0;
    top: 120px;
    width: 784px;
    text-align: center;
    font-family: "Montserrat", Arial, sans-serif;
    font-weight: 500;
    font-size: 28px;
    line-height: 1;
    color: var(--ink);
  }
  .tagline-top {
    position: absolute;
    left: 197px;
    top: 292px;
    font-family: "Montserrat", Arial, sans-serif;
    font-weight: 500;
    font-size: 20px;
    color: var(--text-light);
  }
  .product-title {
    position: absolute;
    left: 197px;
    top: 316px;
    font-family: "Oswald", Impact, sans-serif;
    font-weight: 600;
    font-size: 74px;
    line-height: 1;
    color: var(--text-light);
    letter-spacing: 1px;
  }
  .tagline-bottom {
    position: absolute;
    left: 198px;
    top: 400px;
    font-family: "Montserrat", Arial, sans-serif;
    font-weight: 500;
    font-size: 20px;
    color: var(--text-light);
  }
  .fruit-art {
    position: absolute;
    left: 112px;
    top: 420px;
    width: 235px;
    height: 180px;
  }
  .product-info {
    position: absolute;
    left: 368px;
    top: 497px;
    color: var(--text-light);
  }
  .info-heading {
    font-family: "Oswald", Impact, sans-serif;
    font-weight: 500;
    font-size: 27px;
    line-height: 1;
    letter-spacing: 0.3px;
  }
  .info-line {
    font-family: "Roboto", Arial, sans-serif;
    font-size: 19px;
    line-height: 23px;
  }
  .info-heading + .info-line { margin-top: 6px; }
  .badge {
    position: absolute;
    left: 339px;
    top: 591px;
    width: 22px;
    height: 36px;
    border-radius: 3px;
    background: var(--text-light);
  }
  .volume-box {
    position: absolute;
    left: 369px;
    top: 589px;
    width: 210px;
    height: 39px;
    background: var(--label-white);
    color: var(--ink);
    font-family: "Roboto Condensed", Arial, sans-serif;
    font-size: 27px;
    display: flex;
    align-items: center;
    justify-content: center;
  }
</style>
</head>
<body>
<main class="canvas">
  <section class="label">
    <svg class="label-shapes" width="784" height="705" viewBox="0 0 784 705" aria-hidden="true">
      <defs>
        <linearGradient id="rose-band" x1="0" y1="0" x2="1" y2="0">
          <stop offset="0" stop-color="#a3463a"/>
          <stop offset="0.35" stop-color="#c0685b"/>
          <stop offset="0.72" stop-color="#dc9d92"/>
          <stop offset="1" stop-color="#a3463a"/>
        </linearGradient>
      </defs>
      <path class="rose-band" d="M0 80 Q392 300 784 80 L784 476 L0 476 Z" fill="url(#rose-band)"/>
      <rect class="dark-base" x="0" y="476" width="784" height="229" fill="#231f20"/>
      <path class="notch" d="M497 477 L507 465 L517 477 Z" fill="#231f20"/>
    </svg>

    <p class="brand-name">Meadowlark Scalp Parlour</p>

    <p class="tagline-top">100% PURE &amp; NATURAL</p>
    <h1 class="product-title">JOJOBA OIL</h1>
    <p class="tagline-bottom">REAL INGREDIENTS. REAL RESULTS.</p>

    <svg class="fruit-art" viewBox="0 0 235 180" role="img" aria-label="Illustration of ripe jojoba fruits with green leaves">
      <defs>
        <radialGradient id="fruit-tone" cx="0.45" cy="0.45" r="0.6">
          <stop offset="0" stop-color="#e0704a"/>
          <stop offset="1" stop-color="#8c2a1c"/>
        </radialGradient>
      </defs>
      <ellipse cx="117" cy="100" rx="112" ry="72" fill="url(#fruit-tone)"/>
    </svg>

    <div class="product-info">
      <p class="info-heading">COLD-PRESSED OIL</p>
      <p class="info-line">for skin hair &amp; body</p>
      <p class="info-line">multi-purpose Anti-aging</p>
    </div>

    <div class="badge" aria-hidden="true"></div>
    <div class="volume-box">4fl. oz (118 ml)</div>
  </section>
</main>
</body>
</html>
```